Create a memorable Web Design for real estate branding

we are a Minnepolis brokerage and boutique housing specialist with over 27 years of experience in the Global furnished housing industry, servicing the Greater Los Angeles area. Specializing in “warm environments” we offer a customized approach to satisfying our guests and client’s needs by offering a wide array of options in highly desirable areas. Additionally, Lantern Dwelling Partners offers assistance and expertise to home buyers, sellers and investors.

Industry/Entity Type

Real Estate

Number of Pages Required

1 page

Font styles to use
Serif
Sans Serif
Decorative

```html
<!DOCTYPE html>
<html lang="en">
<head>
<meta charset="utf-8">
<title>Marlow Vale Real Estate</title>
<link href="https://fonts.googleapis.com/css2?family=Lato:wght@400;700&family=Tinos:wght@400;700&display=swap" rel="stylesheet">
<style>
:root{
  --teal:#0aa58a;
  --teal-dark:#087a66;
  --lime:#8cc63f;
  --ink:#222;
  --muted:#777;
  --line:#cfcfcf;
  --field:#fff;
  --paper:#f1f1f1;
  --white:#fff;
}
*{box-sizing:border-box;margin:0;padding:0}
html,body{width:1200px;height:3000px;overflow:hidden;background:var(--white);font-family:"Lato",sans-serif;color:var(--ink)}
.page{position:relative;width:1200px;height:3000px}
.abs{position:absolute}

/* header */
.site-header{left:0;top:0;width:1200px;height:80px;background:var(--white);border-top:4px solid var(--teal)}
.brand{left:160px;top:12px;display:flex;align-items:center;gap:12px;font-family:"Lato",sans-serif;font-weight:700;font-size:24px;line-height:26px;color:var(--teal);letter-spacing:.5px}
.brand-mark{width:16px;height:16px;background:var(--teal);border-radius:50%;flex:none}
.nav{left:0;top:0;width:1200px;height:80px}
.nav a{position:absolute;top:0;height:80px;line-height:84px;font-size:13px;color:#333;text-decoration:none;transform:translateX(-50%);white-space:nowrap}
.nav a.active{left:493px;width:70px;height:88px;background:var(--teal);color:var(--white);font-weight:700;text-align:center;top:-4px;line-height:92px}

/* hero */
.hero{left:0;top:80px;width:1200px;height:410px;background:linear-gradient(180deg,#6f9ad8 0%,#c9d6e6 35%,#e8e4dc 55%,#7aa9c2 78%,#3f7f9e 100%)}
.hero-caption{left:0;top:322px;width:1200px;text-align:center;font-family:"Tinos",serif;font-weight:700;font-size:31px;line-height:44px;color:var(--white);text-shadow:0 2px 4px rgba(0,0,0,.45)}
.hero-arrow{width:48px;height:48px;border-radius:50%;background:rgba(255,255,255,.55);top:262px}

/* section titles */
.section-title{left:0;width:1200px;text-align:center;font-family:"Tinos",serif;font-weight:400;font-size:30px;color:var(--ink)}
.divider{left:530px;width:140px;height:14px}

/* search */
.field{height:36px;background:var(--field);border:1px solid var(--line);font-size:11px;color:#666;padding:0 14px;line-height:34px}
.field svg{position:absolute;right:12px;top:12px}
.search-btn{left:910px;top:632px;width:128px;height:36px;background:var(--teal);color:var(--white);font-weight:700;font-size:15px;text-align:center;line-height:36px}

/* welcome */
.welcome{left:0;top:704px;width:1200px;height:368px;background:linear-gradient(180deg,#8a8d8e 0%,#b9b4a8 45%,#6f7a6e 80%,#56605a 100%)}
.welcome-panel{left:162px;top:750px;width:876px;height:274px;background:rgba(255,255,255,.86);border-radius:8px}
.welcome-text{left:200px;top:844px;width:800px;text-align:center;font-size:11.5px;line-height:21px;color:#333}
.read-more{left:558px;top:970px;width:92px;height:24px;background:var(--teal-dark);color:var(--white);font-size:11px;font-weight:700;text-align:center;line-height:24px}

/* featured */
.featured{left:0;top:1072px;width:1200px;height:448px;background:var(--paper)}
.card{width:276px;height:318px;top:1168px;background:var(--white);box-shadow:0 1px 4px rgba(0,0,0,.15)}
.card-img{position:absolute;left:0;top:0;width:276px;height:150px}
.card-title{position:absolute;left:22px;top:160px;font-weight:700;font-size:15px}
.card-price{position:absolute;left:22px;top:184px;font-weight:700;font-size:14px;color:var(--lime)}
.spec{position:absolute;left:22px;width:232px;height:20px;font-size:11px;font-weight:700;display:flex;align-items:center}
.spec svg{margin-right:14px}
.spec b{margin-left:auto;font-weight:400}
.card-foot{position:absolute;left:0;top:290px;width:276px;border-top:1px solid #e2e2e2;padding:8px 22px;font-size:11px;font-weight:700;display:flex;align-items:center;gap:14px}
.chev{top:1328px}

/* recent */
.recent{left:0;top:1520px;width:1200px;height:406px;background:linear-gradient(180deg,#d8d4cc 0%,#cfc9be 50%,#bdb7ab 100%)}
.rcard{top:1616px;width:280px;height:264px;background:var(--white);overflow:hidden}
.rcard-img{position:absolute;left:0;top:0;width:280px;height:174px}
.rcard-title{position:absolute;left:14px;top:186px;font-weight:700;font-size:15px}
.rcard-sub{position:absolute;left:14px;top:208px;font-size:11px;color:var(--muted)}
.rcard-price{position:absolute;left:14px;top:232px;font-weight:700;font-size:15px;color:var(--lime)}
.rcard-corner{position:absolute;right:0;bottom:0}

.dots{left:368px;top:1952px;display:flex;gap:2px}
.dots span{width:14px;height:14px}
</style>
</head>
<body>
<div class="page">

  <header class="site-header abs">
    <div class="brand abs"><span class="brand-mark"></span><span>Marlow Vale<br>Real Estate</span></div>
    <nav class="nav abs">
      <a class="active">Home</a>
      <a style="left:574px">About Us</a>
      <a style="left:664px">Property</a>
      <a style="left:742px">Blog</a>
      <a style="left:824px">Buyer Info</a>
      <a style="left:924px">Seller Info</a>
      <a style="left:1016px">Contact</a>
    </nav>
  </header>

  <section class="hero abs" role="img" aria-label="Modern luxury home with infinity pool overlooking hills"></section>
  <div class="hero-arrow abs" style="left:90px"><svg width="48" height="48"><path d="M28 16 L20 24 L28 32" stroke="#555" stroke-width="3" fill="none"/></svg></div>
  <div class="hero-arrow abs" style="left:1066px"><svg width="48" height="48"><path d="M20 16 L28 24 L20 32" stroke="#555" stroke-width="3" fill="none"/></svg></div>
  <h1 class="hero-caption abs">We are servicing the Greater<br>Los Angeles area</h1>

  <h2 class="section-title abs" style="top:518px">Quick Search</h2>
  <svg class="divider abs" style="top:560px" viewBox="0 0 140 14"><line x1="0" y1="8" x2="140" y2="8" stroke="#ccc"/><line x1="0" y1="11" x2="140" y2="11" stroke="#ccc"/><path d="M62 12 L70 3 L78 12Z" fill="#0aa58a"/></svg>

  <div class="field abs" style="left:162px;top:586px;width:276px">Location<svg width="12" height="8"><path d="M1 1 L6 6 L11 1" stroke="#333" stroke-width="2" fill="none"/></svg></div>
  <div class="field abs" style="left:462px;top:586px;width:276px">Status<svg width="12" height="8"><path d="M1 1 L6 6 L11 1" stroke="#333" stroke-width="2" fill="none"/></svg></div>
  <div class="field abs" style="left:762px;top:586px;width:276px">Bedrooms<svg width="12" height="8"><path d="M1 1 L6 6 L11 1" stroke="#333" stroke-width="2" fill="none"/></svg></div>
  <div class="field abs" style="left:162px;top:632px;width:276px">Bathrooms<svg width="12" height="8"><path d="M1 1 L6 6 L11 1" stroke="#333" stroke-width="2" fill="none"/></svg></div>
  <div class="field abs" style="left:462px;top:632px;width:128px">Mim Price<svg width="12" height="8"><path d="M1 1 L6 6 L11 1" stroke="#333" stroke-width="2" fill="none"/></svg></div>
  <div class="field abs" style="left:612px;top:632px;width:126px">Max Price<svg width="12" height="8"><path d="M1 1 L6 6 L11 1" stroke="#333" stroke-width="2" fill="none"/></svg></div>
  <div class="field abs" style="left:762px;top:632px;width:126px">Property Type<svg width="12" height="8"><path d="M1 1 L6 6 L11 1" stroke="#333" stroke-width="2" fill="none"/></svg></div>
  <div class="search-btn abs">Search</div>

  <section class="welcome abs" role="img" aria-label="Resort-style home with palm trees and pool terrace"></section>
  <div class="welcome-panel abs"></div>
  <h2 class="section-title abs" style="top:770px">Welcome to Marlow Vale Real Estate</h2>
  <svg class="divider abs" style="top:816px;left:480px;width:240px" viewBox="0 0 240 14" preserveAspectRatio="none"><line x1="0" y1="10" x2="240" y2="10" stroke="#aaa"/><path d="M112 10 L120 2 L128 10Z" fill="#0aa58a"/></svg>
  <p class="welcome-text abs">Fusce elementum, nulla vel pellentes consequat, ante nulla hendrerit arcu, ac tincidunt mauris lacus sed leo. vamus suscipit molestie vestibulum. Lorem ipsum dolor sit amet, Fusce elementum, nulla vel pellentes consequat, ante nulla hendrerit arcu, ac tincidunt mauris lacus sed leo. vamus suscipit molestie. Fusce elementum, nulla vel pellentes consequat, ante nulla hendrerit arcu, ac tincidunt mauris lacus sed leo. vamus suscipit molestie vestibulum. Lorem ipsum dolor sit amet, Fusce elementum, nulla vel pellentes consequat, ante nulla hendrerit arcu, ac tincidunt mauris lacus sed leo. vamus suscipit molestie vestibulum.</p>
  <div class="read-more abs">Read More</div>

  <section class="featured abs"></section>
  <h2 class="section-title abs" style="top:1100px">Featured Property</h2>
  <svg class="divider abs" style="top:1140px" viewBox="0 0 140 14"><line x1="0" y1="8" x2="140" y2="8" stroke="#ccc"/><line x1="0" y1="11" x2="140" y2="11" stroke="#ccc"/><path d="M62 12 L70 3 L78 12Z" fill="#0aa58a"/></svg>
  <svg class="chev abs" style="left:108px" width="24" height="40"><path d="M20 2 L4 20 L20 38" stroke="#bbb" stroke-width="2" fill="none"/></svg>
  <svg class="chev abs" style="left:1068px" width="24" height="40"><path d="M4 2 L20 20 L4 38" stroke="#bbb" stroke-width="2" fill="none"/></svg>

  <article class="card abs" style="left:162px">
    <div class="card-img" role="img" aria-label="Bright bedroom with white sofa and red accents" style="background:linear-gradient(135deg,#8c8a86,#d9d4cf 50%,#b14a52)"></div>
    <h3 class="card-title">Lorem ipsum dolor sit amet,</h3>
    <div class="card-price">$289 / WK</div>
    <div class="spec" style="top:212px"><svg width="16" height="14"><path d="M1 7 H15 V10 Q15 13 11 13 H5 Q1 13 1 10Z M3 7 V2 Q3 0 6 1" stroke="#0aa58a" fill="none" stroke-width="1.4"/></svg>Bathrooms<b>2</b></div>
    <div class="spec" style="top:240px"><svg width="16" height="14"><path d="M1 2 V13 M1 9 H15 V13 M4 8 V5 H9 V8" stroke="#0aa58a" fill="none" stroke-width="1.4"/></svg>Beds<b>2</b></div>
    <div class="spec" style="top:262px"><svg width="16" height="14"><path d="M1 6 L8 1 L15 6 V13 H1Z M4 13 V8 H12 V13" stroke="#0aa58a" fill="none" stroke-width="1.4"/></svg>Garages<b>2</b></div>
    <div class="card-foot"><svg width="10" height="14"><path d="M5 13 Q0 7 0 5 A5 5 0 0 1 10 5 Q10 7 5 13Z" fill="#0aa58a"/><circle cx="5" cy="5" r="2" fill="#fff"/></svg>Duis autem vel,</div>
  </article>

  <article class="card abs" style="left:462px">
    <div class="card-img" role="img" aria-label="Villa with pool at sunset" style="background:linear-gradient(180deg,#3f7fd0,#9cc3e8 45%,#c8a27a 70%,#4a9ab8)"></div>
    <h3 class="card-title">Lorem ipsum dolor sit amet,</h3>
    <div class="card-price">$289 / WK</div>
    <div class="spec" style="top:212px"><svg width="16" height="14"><path d="M1 7 H15 V10 Q15 13 11 13 H5 Q1 13 1 10Z M3 7 V2 Q3 0 6 1" stroke="#0aa58a" fill="none" stroke-width="1.4"/></svg>Bathrooms<b>3</b></div>
    <div class="spec" style="top:240px"><svg width="16" height="14"><path d="M1 2 V13 M1 9 H15 V13 M4 8 V5 H9 V8" stroke="#0aa58a" fill="none" stroke-width="1.4"/></svg>Beds<b>3</b></div>
    <div class="spec" style="top:262px"><svg width="16" height="14"><path d="M1 6 L8 1 L15 6 V13 H1Z M4 13 V8 H12 V13" stroke="#0aa58a" fill="none" stroke-width="1.4"/></svg>Garages<b>2</b></div>
    <div class="card-foot"><svg width="10" height="14"><path d="M5 13 Q0 7 0 5 A5 5 0 0 1 10 5 Q10 7 5 13Z" fill="#0aa58a"/><circle cx="5" cy="5" r="2" fill="#fff"/></svg>Duis autem vel,</div>
  </article>

  <article class="card abs" style="left:762px">
    <div class="card-img" role="img" aria-label="White country house with lawn and trees" style="background:linear-gradient(180deg,#7fa6d6,#c9d6e2 45%,#9a9a86 65%,#5f8a3c)"></div>
    <h3 class="card-title">Lorem ipsum dolor sit amet,</h3>
    <div class="card-price">$289 / WK</div>
    <div class="spec" style="top:212px"><svg width="16" height="14"><path d="M1 7 H15 V10 Q15 13 11 13 H5 Q1 13 1 10Z M3 7 V2 Q3 0 6 1" stroke="#0aa58a" fill="none" stroke-width="1.4"/></svg>Bathrooms<b>4</b></div>
    <div class="spec" style="top:240px"><svg width="16" height="14"><path d="M1 2 V13 M1 9 H15 V13 M4 8 V5 H9 V8" stroke="#0aa58a" fill="none" stroke-width="1.4"/></svg>Beds<b>4</b></div>
    <div class="spec" style="top:262px"><svg width="16" height="14"><path d="M1 6 L8 1 L15 6 V13 H1Z M4 13 V8 H12 V13" stroke="#0aa58a" fill="none" stroke-width="1.4"/></svg>Garages<b>2</b></div>
    <div class="card-foot"><svg width="10" height="14"><path d="M5 13 Q0 7 0 5 A5 5 0 0 1 10 5 Q10 7 5 13Z" fill="#0aa58a"/><circle cx="5" cy="5" r="2" fill="#fff"/></svg>Duis autem vel,</div>
  </article>

  <section class="recent abs" role="img" aria-label="Faded courtyard of a Mediterranean estate"></section>
  <h2 class="section-title abs" style="top:1550px">Recent Property</h2>
  <svg class="divider abs" style="top:1590px" viewBox="0 0 140 14"><path d="M62 12 L70 3 L78 12Z" fill="#0aa58a"/></svg>

  <article class="rcard abs" style="left:162px">
    <div class="rcard-img" role="img" aria-label="Minimal living room with white sofas and tall windows" style="background:linear-gradient(135deg,#e9e2d4,#c9b79a 55%,#2d2a28)"></div>
    <h3 class="rcard-title">Ut wisi enim ad minim</h3>
    <p class="rcard-sub">Lorem ipsum dolor sit amet,</p>
    <div class="rcard-price">$289</div>
    <svg class="rcard-corner" width="20" height="20"><path d="M20 0 V20 H0Z" fill="#0aa58a"/><path d="M14 12 V18 M11 15 H17" stroke="#fff" stroke-width="1.2"/></svg>
  </article>

  <article class="rcard abs" style="left:460px">
    <div class="rcard-img" role="img" aria-label="Stone house with landscaped front garden" style="background:linear-gradient(180deg,#2f6fc4,#8ab0d8 35%,#a4845e 60%,#6b8a4a)"></div>
    <h3 class="rcard-title">Duis autem vel eum iriure dolor</h3>
    <p class="rcard-sub">Lorem ipsum dolor sit amet,</p>
    <div class="rcard-price">$344</div>
    <svg class="rcard-corner" width="20" height="20"><path d="M20 0 V20 H0Z" fill="#0aa58a"/><path d="M14 12 V18 M11 15 H17" stroke="#fff" stroke-width="1.2"/></svg>
  </article>

  <article class="rcard abs" style="left:756px">
    <h3 class="rcard-title">Sed diam nonummy nibh</h3>
    <p class="rcard-sub">Lorem ipsum dolor sit amet,</p>
    <div class="rcard-price">$427</div>
    <svg class="rcard-corner" width="20" height="20"><path d="M20 0 V20 H0Z" fill="#0aa58a"/><path d="M14 12 V18 M11 15 H17" stroke="#fff" stroke-width="1.2"/></svg>
  </article>

  <div class="dots abs"><span style="background:var(--lime)"></span><span style="background:var(--teal)"></span></div>
</div>
</body>
</html>
```